Business card design needed

Double sided
Color, unique, elegant

Maybe put this quote somewhere?? But I think it might make it to cluttered?
“The Pilates Method of Body
Conditioning develops the body
uniformly, corrects posture, restores
vitality, invigorates the mind and
elevates the spirit”
- Walter Brennick

Industry/Entity Type

Business

Contact Information for Business Card

Marta Kovalenko
Pilates Instructor & Personal trainer
Mobile: 0498265043
www.qorvith.com.au
email: qorvithwell.motion@mailvex.com

```html
<!DOCTYPE html>
<html lang="en">
<head>
<meta charset="utf-8">
<title>Qorvith Business Card – Back</title>
<link rel="stylesheet" href="https://fonts.googleapis.com/css2?family=Jost:ital,wght@0,300;0,400;0,700;1,300;1,400;1,700&display=swap">
<style>
  :root {
    --page: #ffffff;
    --card-purple: #57205f;
    --quote-tint: #7a4a84;
    --contact-white: #ffffff;
  }
  html, body {
    margin: 0;
    padding: 0;
    width: 1200px;
    height: 693px;
    overflow: hidden;
    background: var(--page);
  }
  .card-back {
    display: block;
    width: 1200px;
    height: 693px;
  }
  .card-field { fill: var(--card-purple); }
  .quote {
    font-family: "Jost", "Century Gothic", sans-serif;
    fill: var(--quote-tint);
    font-weight: 300;
    font-size: 44px;
  }
  .quote .soft { font-style: italic; font-weight: 300; font-size: 48px; }
  .quote .strong { font-style: italic; font-weight: 700; font-size: 48px; }
  .quote-author {
    font-family: "Jost", "Century Gothic", sans-serif;
    fill: var(--quote-tint);
    font-style: italic;
    font-weight: 700;
    font-size: 52px;
    letter-spacing: 0.04em;
  }
  .contact {
    font-family: "Jost", "Century Gothic", sans-serif;
    fill: var(--contact-white);
    font-weight: 300;
  }
  .contact-web { font-size: 34px; }
  .contact-email { font-size: 29px; font-style: italic; }
  .contact-phone { font-size: 37px; }
</style>
</head>
<body>
<svg class="card-back" viewBox="0 0 1200 693" xmlns="http://www.w3.org/2000/svg">
  <rect class="card-field" x="48" y="47" width="1120" height="607"/>

  <g class="quote" text-anchor="middle">
    <text x="585" y="157">“The Pilates Method of Body</text>
    <text x="585" y="221">Conditioning develops the body</text>
    <text x="585" y="286"><tspan class="soft">uniformly</tspan>, <tspan class="strong">corrects</tspan> posture,</text>
    <text x="585" y="322"><tspan class="strong">restores</tspan></text>
    <text x="585" y="409">vitality, <tspan class="soft">invigorates</tspan> the mind and</text>
    <text x="585" y="472"><tspan class="strong">elevates</tspan> the spirit”</text>
  </g>
  <text class="quote-author" x="1083" y="535" text-anchor="end">- Walter Brennick</text>

  <g class="contact">
    <text class="contact-web" x="309" y="291" textLength="605" lengthAdjust="spacing">www.qorvith.com.au</text>
    <text class="contact-email" x="191" y="345" textLength="840" lengthAdjust="spacing">qorvithwell.motion@mailvex.com</text>
    <text class="contact-phone" x="432" y="440" textLength="356" lengthAdjust="spacing">04•9826•5043</text>
  </g>
</svg>
</body>
</html>
```